Life Coaching business needs a new flyer

We are an Australian business that specialises in Life Coaching, Career Coaching, Health and Wellness Coaching, Yoga and Pilates. We need a A4 double sided flyer that is full colour and folded to DL format. I have attached a couple of designs that I like and some pictures and would like the flyer to be bright yet stylish.

Industry/Entity Type

Life Coaching

```html
<!DOCTYPE html>
<html lang="en">
<head>
<meta charset="utf-8">
<title>Clearpath Coaching – Inside Spread</title>
<link href="https://fonts.googleapis.com/css2?family=Open+Sans:wght@700&family=Raleway:wght@400;500;600;700&display=swap" rel="stylesheet">
<style>
  :root {
    --bg: #ecebe8;
    --paper: #ffffff;
    --heading-blue: #1b8fd8;
    --navy: #1d3c78;
    --band-blue: #2f97da;
    --accent-green: #5db332;
    --ink: #222222;
    --sea-top: #58c3cf;
    --sea-bottom: #9fe0dc;
  }
  * { box-sizing: border-box; margin: 0; padding: 0; }
  html, body { width: 1200px; height: 1000px; overflow: hidden; }
  body { background: var(--bg); font-family: "Raleway", Arial, sans-serif; color: var(--ink); position: relative; }

  .spread { position: absolute; left: 72px; top: 46px; width: 1066px; height: 820px; background: var(--paper); overflow: hidden; box-shadow: 0 4px 14px rgba(0,0,0,.18); }
  .photo { position: absolute; }

  .photo-lagoon { left: 0; top: 0; width: 353px; height: 398px; background: linear-gradient(160deg, var(--sea-top), #7fd3d6 55%, var(--sea-bottom)); }
  .photo-team { left: 0; top: 398px; width: 353px; height: 182px; background: linear-gradient(180deg, #f4f4f4, #e3ddd8); }
  .photo-family { left: 353px; top: 182px; width: 354px; height: 216px; background: linear-gradient(180deg, #a9d3ef 0%, #cfe6f2 45%, #b88a62 75%, #8a6a4c 100%); }
  .photo-yoga { left: 353px; top: 638px; width: 354px; height: 150px; background: linear-gradient(180deg, #2d8ed2, #6cb7e6 70%, #e8eef2); }
  .photo-strip { top: 583px; height: 150px; }
  .strip-1 { left: 707px; width: 118px; background: linear-gradient(180deg, #8ec5ea, #d9748f); }
  .strip-2 { left: 827px; width: 118px; background: linear-gradient(180deg, #e6e2dc, #e59ab8); }
  .strip-3 { left: 947px; width: 119px; background: linear-gradient(160deg, #f2c55a, #9cc06a); }

  .questions { position: absolute; left: 16px; top: 28px; width: 230px; font-family: "Open Sans", Arial, sans-serif; font-weight: 700; font-size: 16.5px; line-height: 19.5px; color: var(--navy); }
  .questions p { margin-bottom: 19px; }

  .section { position: absolute; font-size: 12.3px; line-height: 14.3px; }
  .section h2 { font-weight: 700; font-size: 16px; line-height: 19px; color: var(--heading-blue); margin-bottom: 3px; }
  .section p + p { margin-top: 14px; }

  .about { left: 19px; top: 584px; width: 320px; }
  .about p + p.tight { margin-top: 0; }
  .life { left: 371px; top: 22px; width: 330px; }
  .career { left: 371px; top: 404px; width: 325px; }
  .wellness { left: 371px; top: 551px; width: 325px; }
  .why { left: 727px; top: 22px; width: 320px; }
  .meditation { left: 727px; top: 309px; width: 320px; }
  .yoga { left: 727px; top: 387px; width: 320px; }

  .help-list { list-style: none; margin-top: 16px; margin-left: 20px; font-size: 13.3px; line-height: 15.5px; font-weight: 500; }
  .help-list li { position: relative; padding-left: 13px; margin-bottom: 3.8px; }
  .help-list li::before { content: ""; position: absolute; left: 0; top: 5px; width: 5px; height: 5px; background: var(--heading-blue); }

  .brand { position: absolute; left: 735px; top: 503px; display: flex; align-items: center; gap: 14px; }
  .brand-dot { width: 56px; height: 56px; border-radius: 50%; background: var(--accent-green); }
  .brand-name { font-family: "Raleway", Arial, sans-serif; font-weight: 600; font-size: 24px; line-height: 26px; color: var(--heading-blue); }

  .band { position: absolute; left: 0; top: 0; width: 1066px; height: 820px; pointer-events: none; }

  .contact { position: absolute; right: 30px; top: 753px; text-align: right; color: #fff; font-size: 16px; line-height: 22px; font-weight: 500; }
  .contact .phone { display: inline-flex; align-items: center; gap: 5px; }
</style>
</head>
<body>
  <main class="spread">
    <div class="photo photo-lagoon" role="img" aria-label="Clear turquoise lagoon with a woman relaxing on a pink float"></div>
    <div class="questions">
      <p>Are you looking at making changes this year?</p>
      <p>Are you stuck in a rut or at a crossroad in your life?</p>
      <p>Are you wanting to lose weigh but can’t get motivated?</p>
      <p>Do you have ongoing problems with your career, relationships, or just life itself?</p>
      <p>Life coaching is the answer</p>
    </div>

    <div class="photo photo-team" role="img" aria-label="Cheerful group of business people celebrating"></div>
    <section class="section about">
      <h2>Clearpath Coaching and Meditation Centre</h2>
      <p>Our mission is to help you become the best possible person you can be. Mentally, physically, and spiritually.</p>
      <p>We offer highly qualified and compassionate trainers/coaches for Life Coaching, Meditation, Yoga and Pilates.</p>
      <p class="tight">They will guide and motivate you every step of the way to achieve all your dreams and goals.</p>
      <p>They will make you be the best you can be :)</p>
    </section>

    <section class="section life">
      <h2>Life Coaching</h2>
      <p>Your Life Coach will give you the confidence and the ability to move forward in a positive manner in all areas of your life where you crave change.</p>
      <p>Life Coaching is about breaking down the barriers preventing this change from happening, and creating the ideal environment for positive action to take place. It is a holistic approach, which looks at the present and sets goals for a totally successful future.</p>
    </section>
    <div class="photo photo-family" role="img" aria-label="Smiling family of four by the water"></div>

    <section class="section career">
      <h2>Career Coaching</h2>
      <p>Are you at a crossroads in your career and at a loss about what to do next? Do you want your work to be in alignment with the authentic you? It can be difficult to assess career options, goals, and strategies, and have the confidence to implement changes on your own. With the right coaching support, you will gain the clarity that you need to take control and have a fulfilling and rewarding career.</p>
    </section>
    <section class="section wellness">
      <h2>Wellness Coaching</h2>
      <p>Health and wellness coaches help their clients find the motivation and tools to achieve their health and wellness goals, working with the client to examine and improve the psychological framework that supports those goals.</p>
    </section>
    <div class="photo photo-yoga" role="img" aria-label="Woman in a yoga balance pose against a blue sky"></div>

    <section class="section why">
      <h2>Why Would I Need Help?</h2>
      <p>Coaching is for anyone who wants to make lasting changes in their life. Coaching can assist with such issues as:</p>
      <ul class="help-list">
        <li>Creating a better work- life balance</li>
        <li>Resolving relationship issues</li>
        <li>Career guidance</li>
        <li>Stress management</li>
        <li>Weight loss and fitness</li>
        <li>Motivation and goal setting</li>
        <li>Boosting your self esteem</li>
        <li>Overcoming negative emotions and thoughts</li>
        <li>Better time management</li>
      </ul>
    </section>
    <section class="section meditation">
      <h2>Meditation</h2>
      <p>We specialise in teaching meditation from beginners to advanced and teach a variety of techniques for stress reduction, peace of mind, stillness, and clarity.</p>
    </section>
    <section class="section yoga">
      <h2>Yoga/Pilates</h2>
      <p>Your highly qualified and experienced Yoga or Pilates instructor will come to you and create a fun and varied workout based on what you enjoy and what your goals are.</p>
    </section>

    <div class="brand">
      <span class="brand-dot"></span>
      <span class="brand-name">Clearpath Coaching</span>
    </div>

    <div class="photo photo-strip strip-1" role="img" aria-label="Joyful woman with arms raised beside a pink car"></div>
    <div class="photo photo-strip strip-2" role="img" aria-label="Smiling mature man in a pink shirt"></div>
    <div class="photo photo-strip strip-3" role="img" aria-label="Mother and daughter hugging in sunlight"></div>

    <svg class="band" viewBox="0 0 1066 820" aria-hidden="true">
      <path d="M0,786 Q380,776 707,776 C860,772 960,742 1066,702 L1066,820 L0,820 Z" fill="var(--band-blue)"/>
      <path d="M0,780 Q380,770 707,770 C860,766 960,736 1066,696" fill="none" stroke="var(--accent-green)" stroke-width="5"/>
    </svg>

    <div class="contact">
      <div class="phone">
        <svg width="14" height="14" viewBox="0 0 14 14" aria-hidden="true"><circle cx="7" cy="7" r="6" fill="none" stroke="#fff" stroke-width="1.2"/><path d="M5 4.2c.4-.3.8 0 1 .5l.3.7c.1.3 0 .5-.2.7l-.3.3c.3.7.9 1.3 1.6 1.6l.3-.3c.2-.2.5-.3.7-.2l.7.3c.5.2.8.6.5 1-.4.7-1 .9-1.7.7C6.5 9 5 7.5 4.5 6 4.3 5.3 4.4 4.6 5 4.2z" fill="#fff"/></svg>
        02 9123 4680
      </div>
      <div>www.clearpathcoaching.com.au</div>
    </div>
  </main>
</body>
</html>
```